Redesign of LumoWordfind.com in Bootstrap 4

Current design of LumoWordfind.com is not responsive. We need to change it to latest version of Bootstrap 4 keeping essential elements in place.

Apart from home page, we need designs for http://www.lumowordfind.com/meaning/cat also.

Coding

Number of Pages Required

2 page

Colors
34a7d8

Requirements
Must have
• Bootstrap 4

```html
<!DOCTYPE html>
<html lang="en">
<head>
<meta charset="utf-8">
<title>LumoWordfind – Footer</title>
<link rel="stylesheet" href="https://fonts.googleapis.com/css2?family=Oswald:wght@400&family=Roboto:wght@400;500&display=swap">
<style>
  :root {
    --brand-blue: #34a7d8;
    --footer-bg: #22222a;
    --cell-light: #ffffff;
    --cell-shade: #e0e0e0;
    --letter-ink: #777777;
    --link-ink: #eeeeee;
    --tagline-ink: #e2e2e2;
    --muted-ink: #888890;
    --field-bg: #25252e;
    --field-border: #3b3b45;
    --field-ink: #8a8a92;
  }
  * { box-sizing: border-box; margin: 0; padding: 0; }
  html, body { width: 1200px; height: 427px; overflow: hidden; }
  body { position: relative; font-family: "Roboto", Arial, sans-serif; background: var(--footer-bg); }

  .browse-band {
    position: absolute; left: 0; top: 0; width: 1200px; height: 136px;
    background: var(--brand-blue); border-top: 1px solid #2b8fbb;
  }
  .browse-title {
    position: absolute; left: 0; width: 100%; top: 25px;
    text-align: center; color: #fff;
    font-family: "Oswald", "Arial Narrow", sans-serif; font-weight: 400; font-size: 35px; line-height: 44px;
  }
  .alphabet {
    position: absolute; left: 226px; top: 86px; display: flex; list-style: none;
  }
  .alphabet li {
    width: 28.8px; height: 29px; line-height: 29px; text-align: center;
    font-size: 18px; color: var(--letter-ink); background: var(--cell-light);
  }
  .alphabet li:nth-child(even) { background: var(--cell-shade); }

  .footer-col { position: absolute; top: 168px; }
  .footer-heading {
    color: var(--brand-blue); font-size: 16px; font-weight: 400; line-height: 22px;
    position: relative; padding-bottom: 4px;
  }
  .footer-heading::after {
    content: ""; position: absolute; left: 0; bottom: 0; width: 13px; height: 2px; background: var(--brand-blue);
  }
  .footer-links { list-style: none; margin-top: 20px; }
  .footer-links li { color: var(--link-ink); font-size: 11.5px; font-weight: 500; line-height: 21px; }
  .col-sitemap { left: 142px; }
  .col-legal { left: 377px; }
  .col-others { left: 624px; }
  .col-subscribe { left: 869px; }

  .email-field {
    display: block; margin-top: 20px; width: 200px; height: 40px; padding-left: 10px;
    background: var(--field-bg); border: 1px dashed var(--field-border);
    color: var(--field-ink); font-size: 12.5px; line-height: 38px;
  }
  .submit-btn {
    display: block; margin-top: 11px; width: 200px; height: 27px;
    background: var(--brand-blue); color: #fff; text-align: center;
    font-family: "Oswald", "Arial Narrow", sans-serif; font-size: 15px; line-height: 27px;
  }

  .tagline {
    position: absolute; left: 0; width: 100%; top: 344px; text-align: center;
    font-family: "Oswald", "Arial Narrow", sans-serif; font-size: 21px; line-height: 28px; color: var(--tagline-ink);
  }
  .copyright {
    position: absolute; left: 0; width: 100%; top: 396px; text-align: center;
    font-size: 10px; line-height: 12px; color: var(--muted-ink);
  }
</style>
</head>
<body>
  <header class="browse-band">
    <h2 class="browse-title">Browse Dictionary</h2>
    <ul class="alphabet">
      <li>A</li><li>B</li><li>C</li><li>D</li><li>E</li><li>F</li><li>G</li><li>H</li><li>I</li>
      <li>J</li><li>K</li><li>L</li><li>M</li><li>N</li><li>O</li><li>P</li><li>Q</li><li>R</li>
      <li>S</li><li>T</li><li>U</li><li>V</li><li>W</li><li>X</li><li>Y</li><li>Z</li>
    </ul>
  </header>

  <footer>
    <section class="footer-col col-sitemap">
      <h3 class="footer-heading">Sitemap</h3>
      <ul class="footer-links"><li>FAQ</li><li>Contact</li><li>Blog</li></ul>
    </section>
    <section class="footer-col col-legal">
      <h3 class="footer-heading">Legal</h3>
      <ul class="footer-links"><li>Privacy Policy</li><li>Terms of Use</li></ul>
    </section>
    <section class="footer-col col-others">
      <h3 class="footer-heading">Others</h3>
      <ul class="footer-links"><li>Popular Words</li><li>Common Errors in English</li><li>Tessel Prep Online</li></ul>
    </section>
    <section class="footer-col col-subscribe">
      <h3 class="footer-heading">Subscribe</h3>
      <span class="email-field">Email Id</span>
      <span class="submit-btn">SUBMIT</span>
    </section>

    <p class="tagline">Meaning/Definition, Audio, Phonetics, Usages and more</p>
    <p class="copyright">© 2016. @ LUMO WORDFIND. All Rights Reserved.</p>
  </footer>
</body>
</html>
```